Label design for an exciting new Vodka brand

We need a label design for a dynamic new Vodka brand called 'Pale lantern drift Vodka'. It is a crisp and versatile liquid with a clean and smooth finish. It should appeal to 21-39 year olds, with a slight female skew. Colours, fonts and styles should be modern and relatively neutral - take inspiration from the brand pictures attached.

Target Market(s)

21-39 year olds, both male and female, but with a slight female skew

```html
<!DOCTYPE html>
<html lang="en">
<head>
<meta charset="utf-8">
<title>Pale lantern drift Vodka – Label</title>
<link rel="stylesheet" href="https://fonts.googleapis.com/css2?family=Archivo+Black&family=Raleway:wght@600;700&display=swap">
<style>
  :root {
    --page: #ffffff;
    --navy: #0c3a74;
    --deep-blue: #0d5ba0;
    --mid-blue: #1a70b6;
    --orange: #e84e1b;
    --sky: #95bfe6;
    --ink: #0a0a0a;
    --white: #ffffff;
    --mist: #b9c9d6;
    --bottle-tone: #e8edf2;
  }
  html, body {
    margin: 0;
    padding: 0;
    width: 1200px;
    height: 1190px;
    overflow: hidden;
    background: var(--page);
  }
  .canvas {
    position: relative;
    width: 1200px;
    height: 1190px;
    overflow: hidden;
    background: var(--page);
  }
  .label {
    position: absolute;
    left: 342px;
    top: 197px;
    width: 558px;
    height: 744px;
    overflow: hidden;
    box-shadow: 0 1px 3px rgba(0,0,0,0.12);
  }
  .label-art {
    position: absolute;
    inset: 0;
    width: 100%;
    height: 100%;
    display: block;
  }
  .volume {
    position: absolute;
    left: 146px;
    top: 285px;
    font-family: "Raleway", sans-serif;
    font-weight: 700;
    font-size: 18px;
    color: var(--mist);
  }
  .brand-title {
    position: absolute;
    left: 8px;
    top: 355px;
    margin: 0;
    font-family: "Archivo Black", sans-serif;
    font-weight: 400;
    color: var(--ink);
    letter-spacing: -2px;
  }
  .brand-title span { display: block; white-space: nowrap; }
  .title-line-1 { font-size: 96px; line-height: 96px; }
  .title-line-1 small { font-size: 52px; letter-spacing: -1px; }
  .title-line-2, .title-line-3 { font-size: 96px; line-height: 92px; }
  .description {
    position: absolute;
    left: 333px;
    top: 484px;
    width: 170px;
    margin: 0;
    font-family: "Raleway", sans-serif;
    font-weight: 600;
    font-size: 8.5px;
    line-height: 1.5;
    text-align: center;
    color: var(--white);
  }
  .tagline {
    position: absolute;
    left: 200px;
    top: 691px;
    width: 340px;
    margin: 0;
    font-family: "Raleway", sans-serif;
    font-weight: 700;
    font-size: 14px;
    line-height: 1.35;
    text-align: center;
    color: #eef4fb;
  }
</style>
</head>
<body>
<div class="canvas">
  <section class="label">
    <svg class="label-art" viewBox="0 0 372 496" preserveAspectRatio="none" aria-hidden="false">
      <rect class="backdrop" width="372" height="496" fill="var(--navy)"/>
      <path class="wave-deep" d="M0,80 L372,60 L372,200 C300,205 250,210 190,218 C120,226 60,232 0,230 Z" fill="var(--deep-blue)"/>
      <path class="wave-mid" d="M0,70 L372,50 L372,112 C320,118 260,125 200,128 C130,132 60,136 0,134 Z" fill="var(--mid-blue)"/>
      <path class="wave-orange" d="M0,4 C60,8 110,26 170,32 C240,40 300,36 372,56 L372,62 C320,70 260,84 200,94 C130,104 60,112 0,111 Z" fill="var(--orange)"/>
      <path class="wave-sky" d="M0,462 C80,456 130,440 200,430 C260,420 310,404 372,412 L372,496 L0,496 Z" fill="var(--sky)"/>
      <circle class="bottle-frame" cx="92" cy="94" r="56" fill="none" stroke="var(--white)" stroke-width="3.5"/>
      <rect class="bottle-illustration" x="78" y="72" width="36" height="72" rx="8" fill="var(--bottle-tone)" transform="rotate(25 96 108)" role="img" aria-label="Illustration of a vodka bottle"/>
      <rect class="bottle-fragment" x="58" y="176" width="32" height="24" rx="4" fill="var(--bottle-tone)" transform="rotate(-12 74 188)" role="img" aria-label="Illustration of a bottle base"/>
    </svg>
    <div class="volume">500,ml</div>
    <h1 class="brand-title">
      <span class="title-line-1">Pale <small>lantern</small></span>
      <span class="title-line-2">drift</span>
      <span class="title-line-3">Vodka</span>
    </h1>
    <p class="description">LorLorem ipsum dolor sit amet, consectetuer adipiscing elit, sed diam Lorem ipsum dolor sit amet, consectetuer adipiscing elit, sed diam nonummy nibh euismod tincidunt ut laoreet dolore magna aliquam erat volutpat. Ut wisi enim ad minim veniam, quis nostrud</p>
    <p class="tagline">It is a crisp and versatile<br>liquid with a clean and smooth finish</p>
  </section>
</div>
</body>
</html>
```